Copper Lantern

Need a business card for our restaurant. Restaurant and Bar in the mountains of North Idaho. Rustic looking card

rustic design, wood and metal looking, primarily neutral colors

• Name, address, phone number, website, email address

```html
<!DOCTYPE html>
<html lang="en">
<head>
<meta charset="utf-8">
<title>Copper Lantern – Business Card</title>
<link rel="stylesheet" href="https://fonts.googleapis.com/css2?family=Montserrat:wght@400;500;700&display=swap">
<style>
  :root {
    --bg: #2b2b2b;
    --card: #151515;
    --card-edge: #1d1d1d;
    --ink: #ffffff;
    --ink-soft: #e6e6e6;
    --emboss: #8a8a8a;
    --emboss-dim: #3c3c3c;
  }
  * { margin: 0; padding: 0; box-sizing: border-box; }
  html, body {
    width: 1200px; height: 689px; overflow: hidden;
    background: var(--bg);
    font-family: "Montserrat", Arial, sans-serif;
  }
  .canvas { position: relative; width: 1200px; height: 689px; }
  .card {
    position: absolute; top: 190px;
    width: 540px; height: 309px;
    background: var(--card);
    border-radius: 24px;
    border: 1px solid var(--card-edge);
    box-shadow: 0 20px 40px rgba(0,0,0,.45);
  }
  .card--back { left: 30px; }
  .card--front { left: 630px; }

  .badge {
    position: absolute;
    width: 200px; height: 200px;
    border-radius: 50%;
    display: flex; align-items: center; justify-content: center;
    text-align: center;
  }
  .card--back .badge {
    left: 170px; top: 54px;
    border: 5px solid var(--emboss);
    box-shadow: inset 0 0 0 1px var(--emboss-dim);
  }
  .card--front .badge {
    left: 38px; top: 64px;
    border: 4px solid var(--ink);
  }
  .badge__name {
    font-weight: 500;
    font-size: 20px;
    letter-spacing: 3px;
    line-height: 1.35;
    text-transform: uppercase;
  }
  .card--back .badge__name { color: var(--emboss); }
  .card--front .badge__name { color: var(--ink); }

  .divider {
    position: absolute; left: 272px; top: 54px;
    width: 2px; height: 200px;
    background: var(--ink);
  }
  .contact {
    position: absolute; left: 296px; top: 54px;
    color: var(--ink-soft);
    font-size: 13px; line-height: 1.55;
  }
  .contact__name {
    font-weight: 700; font-size: 25px; color: var(--ink);
    line-height: 1.1;
  }
  .contact__title { margin-bottom: 12px; }
  .contact__address { margin-bottom: 12px; }
  .contact__row { display: flex; align-items: center; gap: 8px; }
  .contact__row svg { width: 12px; height: 12px; flex: none; fill: var(--ink); }
</style>
</head>
<body>
<main class="canvas">
  <section class="card card--back" aria-label="Card back">
    <div class="badge"><span class="badge__name">Copper<br>Lantern</span></div>
  </section>

  <section class="card card--front" aria-label="Card front">
    <div class="badge"><span class="badge__name">Copper<br>Lantern</span></div>
    <div class="divider"></div>
    <div class="contact">
      <p class="contact__name">Owen Hartley</p>
      <p class="contact__title">Managing Director</p>
      <p class="contact__address">Your address, City<br>State, Zip 1234</p>
      <p class="contact__row">
        <svg viewBox="0 0 24 24" aria-hidden="true"><path d="M6.6 10.8a15.1 15.1 0 0 0 6.6 6.6l2.2-2.2a1 1 0 0 1 1-.25 11.4 11.4 0 0 0 3.6.57 1 1 0 0 1 1 1V20a1 1 0 0 1-1 1A17 17 0 0 1 3 4a1 1 0 0 1 1-1h3.5a1 1 0 0 1 1 1c0 1.25.2 2.45.57 3.6a1 1 0 0 1-.25 1z"/></svg>
        123 456 789
      </p>
      <p class="contact__row">
        <svg viewBox="0 0 24 24" aria-hidden="true"><path d="M2 5h20v14H2zm2 2v.5l8 5 8-5V7l-8 5z"/></svg>
        info@yourgmail.com
      </p>
      <p class="contact__row">
        <svg viewBox="0 0 24 24" aria-hidden="true"><path d="M12 2a10 10 0 1 0 0 20 10 10 0 0 0 0-20zm0 2c.9 1.2 1.6 2.9 1.9 5h-3.8c.3-2.1 1-3.8 1.9-5zM4.3 11h3.8c.1 1.9.4 3.6 1 5H5.6a8 8 0 0 1-1.3-5zm5.8 0h3.8c-.1 2-.5 3.7-1.9 5.5-1.4-1.8-1.8-3.5-1.9-5.5zm5.8 0h3.8a8 8 0 0 1-1.3 5h-3.5c.6-1.4.9-3.1 1-5z"/></svg>
        www.yourwebsite.com
      </p>
    </div>
  </section>
</main>
</body>
</html>
```